Interior designer needs a power point template design

I need a template PowerPoint design for my client presentations. The presentations I prepare for my clients usually include the furniture project, the detail of the selected furniture, and the costs. There are a lot of images I insert. What I need is to have a template that I can use for all my presentations, where from time to time I will insert the specific images and descriptions I want to insert. What will always be the same will be the cover, the colors, the font, and the design of the internal sections.
I already have my logo that I would like to insert on each page of the presentation (in small size).
In summary, I need:
- basic template design
- cover with an image chosen by Pictavale photo
- design an internal section/chapter
- internal page design.

I like the clolors of pink and brown <8please see image attached)
Images (will come from Pictavale photo)
● entrance/hall
● living room
● dining room
● Bathroom
● Closet
● Kids room
● Master bedroom
● Master bathroom
● Kitchen
● Office
● Laundry
● Balcony or Terrace

Target Market(s)

Customers (both residential and commercial projects)

Industry/Entity Type

interior design

Font styles to use
Other font styles liked:
• I like courier new

Requirements
Must have
• beautiful design
Should not have
• animations

```html
<!DOCTYPE html>
<html lang="it">
<head>
<meta charset="utf-8">
<title>Casa Lumen – Presentation Template</title>
<link rel="stylesheet" href="https://fonts.googleapis.com/css2?family=Montserrat:wght@300;400;500&display=swap">
<style>
  :root {
    --terracotta: #c58a78;
    --paper: #ffffff;
    --stone: #d6d5d4;
    --ink: #2b2b2b;
    --ink-soft: #3a3a3a;
    --canvas: #ffffff;
  }
  * { box-sizing: border-box; margin: 0; padding: 0; }
  html, body {
    width: 1200px; height: 1060px; overflow: hidden;
    background: var(--canvas);
    font-family: "Montserrat", sans-serif;
  }
  .board { position: relative; width: 1200px; height: 1060px; }
  .slide {
    position: absolute; width: 488px; height: 274px; overflow: hidden;
    background: var(--paper);
    box-shadow: 0 2px 14px rgba(0,0,0,0.14);
  }
  .slide--cover   { left: 71px;  top: 77px; }
  .slide--chapter { left: 638px; top: 77px; background: var(--terracotta); }
  .slide--gallery { left: 71px;  top: 392px; }
  .slide--detail  { left: 638px; top: 392px; }
  .slide--feature { left: 71px;  top: 706px; }

  .block { position: absolute; background: var(--terracotta); }
  .photo { position: absolute; }

  .title {
    position: absolute; font-weight: 400; font-size: 22px;
    letter-spacing: 0.16em; line-height: 1.4; white-space: nowrap;
  }
  .title--light { color: var(--paper); }
  .title--dark { color: var(--ink); }

  .body-copy {
    position: absolute; font-size: 6.4px; line-height: 10px; font-weight: 400;
  }
  .body-copy--light { color: var(--paper); }
  .body-copy--dark { color: var(--ink-soft); }

  .caption {
    position: absolute; font-size: 8.6px; letter-spacing: 0.24em;
    line-height: 12px; font-weight: 400; text-transform: uppercase;
  }

  /* Brand mark: plain circle + name */
  .brand { position: absolute; display: flex; flex-direction: column; align-items: center; color: var(--ink); }
  .brand__circle { border: 1px solid var(--ink); border-radius: 50%; }
  .brand__name { font-weight: 300; letter-spacing: 0.12em; text-align: center; line-height: 1.15; white-space: nowrap; }

  .brand--large { left: 0; width: 488px; top: 62px; }
  .brand--large .brand__circle { width: 84px; height: 84px; margin-bottom: 14px; }
  .brand--large .brand__name { font-size: 24px; }
  .brand--large .brand__sub { font-size: 6px; letter-spacing: 0.55em; font-weight: 300; margin-top: 6px; }

  .brand--small { width: 48px; }
  .brand--small .brand__circle { width: 34px; height: 34px; margin-bottom: 5px; }
  .brand--small .brand__name { font-size: 8px; }
  .brand--small .brand__sub { font-size: 3px; letter-spacing: 0.25em; font-weight: 300; margin-top: 2px; }

  .feature-panel { position: absolute; left: 0; top: 16px; width: 211px; height: 242px; background: var(--terracotta); }
  .feature-frame { position: absolute; left: 9px; top: 22px; width: 208px; height: 230px; border: 1px solid var(--paper); }
</style>
</head>
<body>
<main class="board">

  <!-- Cover -->
  <section class="slide slide--cover">
    <div class="block" style="left:0;top:0;width:89px;height:66px;"></div>
    <div class="block" style="left:406px;top:205px;width:82px;height:69px;"></div>
    <div class="brand brand--large">
      <div class="brand__circle"></div>
      <div class="brand__name">CASA LUMEN</div>
      <div class="brand__sub">INTERIOR DESIGN</div>
    </div>
  </section>

  <!-- Chapter: Camera padronale -->
  <section class="slide slide--chapter">
    <div class="photo" role="img" aria-label="Illustrazione di un ingresso con attaccapanni e porte"
         style="left:90px;top:0;width:111px;height:195px;background:linear-gradient(180deg,#e9c98f 0%,#c9a06a 45%,#8c4a3a 70%,#e2ad6e 100%);"></div>
    <div class="block" style="left:0;top:235px;width:43px;height:39px;background:var(--stone);"></div>
    <h2 class="title title--light" style="left:112px;top:48px;">CAMERA PADRONALE</h2>
    <div class="brand brand--small" style="left:430px;top:10px;">
      <div class="brand__circle"></div>
      <div class="brand__name">CASA<br>LUMEN</div>
      <div class="brand__sub">INTERIOR DESIGN</div>
    </div>
    <p class="body-copy body-copy--light" style="left:291px;top:111px;width:158px;">
      Perspiciatis unde omnis iste natus error sit voluptatem accusantium doloremque laudantium, totam rem aperiam, eaque ipsa quae ab illo inventore veritatis et quasi architecto beatae vitae dicta sunt explicabo. Nemo enim ipsam voluptatem quia voluptas sit aspernatur aut odit aut fugit, sed quia consequuntur magni dolores eos qui ratione voluptatem sequi nesciunt. Neque porro quisquam est, qui dolorem ipsum quia dolor sit amet, consectetur, adipisci velit, sed quia non numquam eius modi tempora incidunt ut labore et dolore magnam
    </p>
    <p class="caption" style="left:53px;top:241px;color:var(--paper);">L’arredamento<br>della camera padronale</p>
  </section>

  <!-- Internal page: gallery -->
  <section class="slide slide--gallery">
    <div class="block" style="left:0;top:0;width:488px;height:168px;"></div>
    <h2 class="title title--light" style="left:112px;top:30px;">CAMERA PADRONALE</h2>
    <div class="brand brand--small" style="left:430px;top:10px;">
      <div class="brand__circle"></div>
      <div class="brand__name">CASA<br>LUMEN</div>
      <div class="brand__sub">INTERIOR DESIGN</div>
    </div>
    <div class="photo" role="img" aria-label="Illustrazione di una cucina con mobili in legno"
         style="left:0;top:82px;width:222px;height:151px;background:linear-gradient(180deg,#f3e2cf 0%,#efd7bf 50%,#c08a55 70%,#4f8b87 100%);"></div>
    <div class="photo" role="img" aria-label="Illustrazione di una sala da pranzo con tavolo e sedie"
         style="left:265px;top:82px;width:223px;height:151px;background:linear-gradient(180deg,#f2d8ac 0%,#e7b77a 55%,#cf8c45 100%);"></div>
    <p class="caption" style="left:53px;top:241px;color:var(--ink-soft);">L’arredamento<br>della camera padronale</p>
    <p class="body-copy body-copy--dark" style="left:304px;top:240px;width:160px;">
      Perspiciatis unde omnis iste natus error sit voluptatem accusantium doloremque laudantium, totam rem aperiam.
    </p>
  </section>

  <!-- Internal page: detail -->
  <section class="slide slide--detail">
    <div class="block" style="left:330px;top:0;width:158px;height:274px;"></div>
    <div class="photo" role="img" aria-label="Illustrazione di un bagno con piastrelle azzurre e vasca"
         style="left:224px;top:57px;width:264px;height:160px;background:linear-gradient(180deg,#5fb9c4 0%,#4fb0bd 65%,#c9d3d6 100%);"></div>
    <h2 class="title title--dark" style="left:26px;top:16px;">CABINA ARMADIO</h2>
    <p class="body-copy body-copy--dark" style="left:26px;top:99px;width:155px;font-size:7.3px;line-height:12.4px;">
      Perspiciatis unde omnis iste natus error sit voluptatem accusantium doloremque laudantium, totam rem aperiam, eaque ipsa quae ab illo inventore veritatis et quasi architecto beatae vitae dicta sunt explicabo.
    </p>
    <div class="brand brand--small" style="left:20px;top:198px;">
      <div class="brand__circle"></div>
      <div class="brand__name">CASA<br>LUMEN</div>
      <div class="brand__sub">INTERIOR DESIGN</div>
    </div>
  </section>

  <!-- Section feature -->
  <section class="slide slide--feature">
    <div class="photo" role="img" aria-label="Illustrazione di un ufficio open space con grandi vetrate"
         style="left:0;top:0;width:488px;height:274px;background:linear-gradient(160deg,#e4e7ec 0%,#b9c3d1 35%,#7ea9d6 55%,#5d6e8c 80%,#6a6f80 100%);"></div>
    <div class="feature-panel"></div>
    <div class="feature-frame"></div>
    <h2 class="title title--light" style="left:24px;top:38px;line-height:31px;">BAGNO<br>PADRONALE</h2>
    <p class="body-copy body-copy--light" style="left:24px;top:125px;width:160px;">
      Perspiciatis unde omnis iste natus error sit volupt atem accusantium doloremque laudantium, totam rem aperiam.
    </p>
    <div class="brand brand--small" style="left:18px;top:176px;">
      <div class="brand__circle"></div>
      <div class="brand__name">CASA<br>LUMEN</div>
      <div class="brand__sub">INTERIOR DESIGN</div>
    </div>
  </section>

</main>
</body>
</html>
```